TA BRAMLEY BUSINESS CARD DESIGN PROJECT

We need to utilize our logo that was expertly created on PixelHarbor and now need to match this with a business card design.

```html
<!DOCTYPE html>
<html lang="en">
<head>
<meta charset="utf-8">
<title>TA Bramley Business Card</title>
<link rel="stylesheet" href="https://fonts.googleapis.com/css2?family=Open+Sans:wght@400;600;700&display=swap">
<style>
  :root {
    --backdrop: #3a3a3a;
    --card: #161616;
    --card-deep: #0f0f0f;
    --pattern-mid: #2a2a2a;
    --accent: #1a5fc4;
    --ink: #e6e6e6;
  }
  * { margin: 0; padding: 0; box-sizing: border-box; }
  html, body {
    width: 1200px; height: 801px; overflow: hidden;
    background: var(--backdrop);
    font-family: "Open Sans", Arial, sans-serif;
  }
  .sheet {
    width: 1200px; height: 801px;
    display: flex; align-items: center; justify-content: center; gap: 60px;
  }
  .card {
    position: relative;
    width: 520px; height: 297px;
    background: var(--card);
    border-bottom: 2px solid var(--accent);
    border-left: 2px solid var(--accent);
    overflow: hidden;
  }
  .brand {
    position: absolute; top: 44px; right: 56px;
    color: var(--accent); font-weight: 700;
    font-size: 34px; letter-spacing: 3px;
  }
  .divider-long {
    position: absolute; top: 118px; left: 150px; right: 40px;
    height: 1px; background: var(--accent);
  }
  .address {
    position: absolute; top: 134px; right: 40px;
    color: var(--ink); font-size: 13px; line-height: 1.45; text-align: right;
  }
  .person { position: absolute; left: 40px; top: 180px; }
  .person-name {
    color: var(--accent); font-weight: 700; font-size: 19px; letter-spacing: .5px;
  }
  .person-role { color: var(--ink); font-size: 13px; margin-top: 1px; }
  .divider-short {
    position: absolute; left: 40px; top: 232px; width: 230px;
    height: 1px; background: var(--accent);
  }
  .contacts {
    position: absolute; left: 40px; top: 240px; list-style: none;
    color: var(--ink); font-size: 12.5px; line-height: 1.45;
  }
  .contacts li { display: flex; align-items: center; gap: 8px; }
  .contacts svg { width: 10px; height: 10px; fill: var(--accent); flex: none; }
  .card-back { background: var(--card-deep); }
  .back-pattern {
    position: absolute; inset: 0;
    background: linear-gradient(135deg, var(--card-deep) 0%, var(--card) 45%, var(--pattern-mid) 100%);
  }
  .back-brand {
    position: absolute; right: 110px; top: 180px;
    color: var(--accent); font-weight: 700; font-size: 22px; letter-spacing: 2px;
  }
</style>
</head>
<body>
  <main class="sheet">
    <section class="card card-front">
      <div class="brand">TA BRAMLEY</div>
      <div class="divider-long"></div>
      <p class="address">1180 Harbor Crest Way<br>Marin Cove CA 90410</p>
      <div class="person">
        <h1 class="person-name">DORIAN VALE</h1>
        <p class="person-role">President</p>
      </div>
      <div class="divider-short"></div>
      <ul class="contacts">
        <li><svg viewBox="0 0 10 10"><path d="M2 0h2l1 3-1.5 1a6 6 0 0 0 2.5 2.5L7 5l3 1v2a2 2 0 0 1-2 2A8 8 0 0 1 0 2a2 2 0 0 1 2-2z"/></svg>555-310-4827</li>
        <li><svg viewBox="0 0 10 10"><path d="M0 2h10v6H0z M0 2l5 3.5L10 2" /></svg>d.vale@tabramley.com</li>
        <li><svg viewBox="0 0 10 10"><circle cx="5" cy="5" r="5"/></svg>www.tabramley.com</li>
      </ul>
    </section>
    <section class="card card-back">
      <div class="back-pattern" role="img" aria-label="Tone-on-tone repeating brand pattern in dark greys"></div>
      <div class="back-brand">TA BRAMLEY</div>
    </section>
  </main>
</body>
</html>
```